Meadowlark Property Review is a leading provider of residential appraisal and home inspection products in S

I need a business card/logo designed that obviously describes my business. We are a residential appraisal and home inspection company in Springfield, MO. We offer residential appraisals, home inspection, pest inspection and radon gas measurement. We have been in business for 18 years and hold state certified residential appraisal licenses and OBREX certified home inspection licenses. I have a logo that I really like and will attach, but would be open to new suggestions. I like more modern designs than traditional and would like a two sided card with our services, licenses and qualifications on the back.

```html
<!DOCTYPE html>
<html lang="en">
<head>
<meta charset="utf-8">
<title>Meadowlark Property Review – Business Card</title>
<link rel="stylesheet" href="https://fonts.googleapis.com/css2?family=Source+Sans+3:wght@400;600;700&display=swap">
<style>
  :root {
    --canvas: #e9e6e2;
    --card-white: #ffffff;
    --card-dark: #2a221d;
    --orange: #f39a2b;
    --orange-light: #f6ad4a;
    --brown: #8c6a4b;
    --ink: #1f1a17;
    --paper: #f4f1ee;
  }
  * { box-sizing: border-box; margin: 0; padding: 0; }
  html, body { width: 1200px; height: 892px; overflow: hidden; }
  body {
    background: var(--canvas);
    font-family: "Source Sans 3", "Myriad Pro", sans-serif;
    position: relative;
  }
  .card {
    position: absolute;
    left: 290px;
    width: 620px;
    height: 354px;
    border-radius: 4px;
    overflow: hidden;
    box-shadow: 0 6px 18px rgba(0,0,0,.18);
  }
  .card--front { top: 62px; background: var(--card-white); }
  .card--back  { top: 476px; background: linear-gradient(135deg, #332922 0%, var(--card-dark) 55%, #231c18 100%); }

  /* front */
  .band { position: absolute; height: 34px; background: var(--orange); }
  .band--top {
    top: 0; left: 0; width: 330px;
    background: linear-gradient(90deg, var(--orange) 0%, var(--orange-light) 100%);
    clip-path: polygon(0 0, 100% 0, 88% 100%, 0 100%);
  }
  .band--bottom {
    bottom: 0; right: 0; width: 350px;
    clip-path: polygon(8% 0, 100% 0, 100% 100%, 0 100%);
  }
  .contact {
    position: absolute; left: 38px; top: 118px;
    list-style: none; color: var(--ink);
    font-size: 17px; line-height: 22px;
  }
  .contact li { display: flex; align-items: center; gap: 10px; height: 22px; }
  .contact__icon {
    width: 17px; height: 17px; background: var(--orange);
    display: inline-flex; align-items: center; justify-content: center; flex: none;
  }
  .contact__icon svg { width: 12px; height: 12px; fill: #fff; }
  .contact__spacer { width: 17px; flex: none; }

  .brand {
    position: absolute; display: flex; align-items: center; gap: 10px;
  }
  .brand--front { left: 330px; top: 132px; }
  .brand--back  { left: 404px; top: 148px; }
  .brand__mark { width: 16px; height: 16px; background: var(--orange); flex: none; }
  .brand__name {
    font-weight: 700; font-size: 27px; line-height: 29px; color: var(--brown);
  }
  .brand--back .brand__name { color: var(--paper); font-size: 24px; line-height: 27px; }

  /* back */
  .services {
    position: absolute; right: 262px; top: 22px; text-align: right; color: var(--paper);
  }
  .services__title { font-weight: 400; font-size: 34px; line-height: 40px; margin-bottom: 4px; }
  .services__list { list-style: none; font-size: 15.5px; line-height: 24.5px; }
  .services__list li { display: flex; justify-content: flex-end; align-items: center; gap: 10px; }
  .services__list svg { width: 14px; height: 10px; flex: none; }
  .divider {
    position: absolute; left: 384px; top: 30px; width: 3px; height: 294px; background: var(--paper);
  }
</style>
</head>
<body>

<section class="card card--front" aria-label="Card front">
  <div class="band band--top"></div>
  <div class="band band--bottom"></div>

  <ul class="contact">
    <li><span class="contact__icon"><svg viewBox="0 0 12 12"><path d="M2.5 1l2 2-1 1.3a6.5 6.5 0 0 0 4.2 4.2L9 7.5l2 2-1.3 1.5C5.5 11 1 6.5 1 2.3z"/></svg></span>417-555-0142</li>
    <li><span class="contact__icon"><svg viewBox="0 0 12 12"><path d="M3.5 0.5h5v11h-5z M4.5 1.5v7.5h3V1.5z"/></svg></span>417-555-0187</li>
    <li><span class="contact__icon"><svg viewBox="0 0 12 12"><path d="M3 1h6v3H3z M1 5h10v5H9V8H3v2H1z M4 9h4v2H4z"/></svg></span>417-555-0119</li>
    <li><span class="contact__icon"><svg viewBox="0 0 12 12"><path d="M1 2.5h10v7H1z M1.6 3l4.4 3.4L10.4 3" fill="none" stroke="#fff" stroke-width="1"/></svg></span>info@meadowlarkreview.com</li>
    <li><span class="contact__icon"><svg viewBox="0 0 12 12"><path d="M6 1l5 4.6h-1.5V11h-2.5V8H5v3H2.5V5.6H1z"/></svg></span>Meadowlark Property Review</li>
    <li><span class="contact__spacer"></span>482 E Larkspur Road; Suite B</li>
    <li><span class="contact__spacer"></span>Springfield, MO 65810</li>
  </ul>

  <div class="brand brand--front">
    <span class="brand__mark"></span>
    <span class="brand__name">Meadowlark<br>Property Review</span>
  </div>
</section>

<section class="card card--back" aria-label="Card back">
  <div class="services">
    <h2 class="services__title">Services</h2>
    <ul class="services__list">
      <li>home inspection<svg viewBox="0 0 14 10"><path d="M1 5l4 4 8-8" fill="none" stroke="var(--orange)" stroke-width="2.2"/></svg></li>
      <li>property inspection<svg viewBox="0 0 14 10"><path d="M1 5l4 4 8-8" fill="none" stroke="var(--orange)" stroke-width="2.2"/></svg></li>
      <li>residential appraisal<svg viewBox="0 0 14 10"><path d="M1 5l4 4 8-8" fill="none" stroke="var(--orange)" stroke-width="2.2"/></svg></li>
      <li>termite inspection<svg viewBox="0 0 14 10"><path d="M1 5l4 4 8-8" fill="none" stroke="var(--orange)" stroke-width="2.2"/></svg></li>
      <li>radon gas measurement<svg viewBox="0 0 14 10"><path d="M1 5l4 4 8-8" fill="none" stroke="var(--orange)" stroke-width="2.2"/></svg></li>
      <li>pre purchase inspection<svg viewBox="0 0 14 10"><path d="M1 5l4 4 8-8" fill="none" stroke="var(--orange)" stroke-width="2.2"/></svg></li>
      <li>thermal imaging<svg viewBox="0 0 14 10"><path d="M1 5l4 4 8-8" fill="none" stroke="var(--orange)" stroke-width="2.2"/></svg></li>
      <li>mechanical inspection<svg viewBox="0 0 14 10"><path d="M1 5l4 4 8-8" fill="none" stroke="var(--orange)" stroke-width="2.2"/></svg></li>
      <li>tax appeal<svg viewBox="0 0 14 10"><path d="M1 5l4 4 8-8" fill="none" stroke="var(--orange)" stroke-width="2.2"/></svg></li>
      <li>asset evaluation<svg viewBox="0 0 14 10"><path d="M1 5l4 4 8-8" fill="none" stroke="var(--orange)" stroke-width="2.2"/></svg></li>
      <li>energy audits<svg viewBox="0 0 14 10"><path d="M1 5l4 4 8-8" fill="none" stroke="var(--orange)" stroke-width="2.2"/></svg></li>
    </ul>
  </div>
  <div class="divider"></div>
  <div class="brand brand--back">
    <span class="brand__name">Meadowlark<br>Property Review</span>
  </div>
</section>

</body>
</html>
```